Tallowmere Air Business Card Design

Design new, 2 sides, business cards for a residential and light commercial heating, air conditioning contractor.

Target Market(s)

Homeowners, small businesses

Industry/Entity Type

Business

Contact Information for Business Card

Dominic Westerhall
Phone - 862-415-2736
Email
Address - PO box 518
Brightwater NJ 07912
Website - www.HarborBreezeLLC.example

Requirements
Must have
• logo, company colors, standard size with no die cut, so I can use nova stamp

```html
<!DOCTYPE html>
<html lang="en">
<head>
<meta charset="utf-8">
<title>Tallowmere Air Business Card</title>
<link href="https://fonts.googleapis.com/css2?family=Open+Sans:ital,wght@0,400;0,700;1,400&display=swap" rel="stylesheet">
<style>
  :root {
    --maroon: #9b1f32;
    --orange: #f7941d;
    --ink: #4a4a4a;
    --paper: #ffffff;
    --backdrop: #e9e7e4;
  }
  * { margin: 0; padding: 0; box-sizing: border-box; }
  html, body { width: 1200px; height: 987px; overflow: hidden; }
  body {
    background: var(--backdrop);
    font-family: "Open Sans", sans-serif;
    position: relative;
  }
  .card {
    position: absolute;
    left: 292px;
    width: 616px;
    height: 352px;
    overflow: hidden;
    box-shadow: 0 2px 6px rgba(0,0,0,0.18);
  }
  .card-front { top: 130px; background: var(--paper); }
  .card-back { top: 505px; background: var(--orange); }

  .brand {
    position: absolute;
    display: flex;
    align-items: center;
    gap: 8px;
    color: var(--maroon);
    font-weight: 700;
    font-size: 25px;
    white-space: nowrap;
    transform: translate(-50%, -50%);
  }
  .brand-dot {
    width: 14px; height: 14px;
    border-radius: 50%;
    background: var(--maroon);
  }
  .card-front .brand { left: 483px; top: 88px; }
  .card-back .brand { left: 487px; top: 257px; }

  .person-name {
    position: absolute; left: 35px; top: 143px;
    color: var(--maroon); font-weight: 700; font-size: 21px; letter-spacing: 0.2px;
  }
  .person-title {
    position: absolute; left: 35px; top: 170px;
    color: var(--orange); font-size: 16px;
  }
  .divider {
    position: absolute; left: 35px; top: 194px;
    width: 549px; height: 1.5px; background: var(--orange);
  }
  .contact-list {
    position: absolute; left: 35px; top: 210px;
    list-style: none; color: var(--ink); font-size: 15.5px;
  }
  .contact-list li {
    display: flex; align-items: center; gap: 9px; height: 22px;
  }
  .contact-list svg { width: 15px; height: 15px; fill: var(--maroon); flex: none; }
  .address {
    position: absolute; right: 32px; top: 255px;
    text-align: right; color: var(--ink); font-size: 15.5px; line-height: 22px;
    font-style: normal;
  }
  .footer-bands {
    position: absolute; left: 0; bottom: 0; width: 616px; height: 37px;
  }
  .website {
    position: absolute; right: 35px; bottom: 8px;
    color: var(--paper); font-style: italic; font-size: 15.5px; letter-spacing: 0.3px;
  }
</style>
</head>
<body>

<section class="card card-front" aria-label="Business card front">
  <div class="brand"><span class="brand-dot"></span>Tallowmere Air</div>

  <h1 class="person-name">DOMINIC WESTERHALL</h1>
  <p class="person-title">CEO/Founder</p>
  <div class="divider"></div>

  <ul class="contact-list">
    <li>
      <svg viewBox="0 0 16 16" aria-hidden="true"><path d="M3.5 1.5l2.5 0 1.2 3.3-1.6 1.2c.8 1.8 2.2 3.2 4 4l1.2-1.6 3.3 1.2v2.5c0 .8-.7 1.5-1.5 1.5C6.9 13.6 2.4 9.1 2 3c0-.8.7-1.5 1.5-1.5z"/></svg>
      862 415 2736
    </li>
    <li>
      <svg viewBox="0 0 16 16" aria-hidden="true"><path d="M4.5 0.5h7c.6 0 1 .4 1 1v13c0 .6-.4 1-1 1h-7c-.6 0-1-.4-1-1v-13c0-.6.4-1 1-1zm1 2v9.5h5V2.5h-5zm2.5 10.5a.9.9 0 100 1.8.9.9 0 000-1.8z"/></svg>
      862 415 2791
    </li>
    <li>
      <svg viewBox="0 0 16 16" aria-hidden="true"><path d="M4 1h8v4H4zM1.5 6h13c.6 0 1 .4 1 1v5h-3v3h-9v-3h-3V7c0-.6.4-1 1-1zm3 6.5v1.5h7v-1.5z"/></svg>
      862 415 2740
    </li>
    <li>
      <svg viewBox="0 0 16 16" aria-hidden="true"><path d="M1 3.5h14v9H1zm1.3 1l5.7 4.3 5.7-4.3z"/></svg>
      name@tallowmereair.example
    </li>
  </ul>

  <address class="address">
    PO box 518<br>
    Brightwater NJ 07912
  </address>

  <svg class="footer-bands" viewBox="0 0 616 37" aria-hidden="true">
    <rect x="0" y="23" width="345" height="14" fill="var(--maroon)"/>
    <polygon points="333,37 355,0 616,0 616,37" fill="var(--orange)"/>
  </svg>
  <span class="website">tallowmereair.example</span>
</section>

<section class="card card-back" aria-label="Business card back">
  <div class="brand"><span class="brand-dot"></span>Tallowmere Air</div>
</section>

</body>
</html>
```